Plotvista Caribbean

We need a vibrant, user friendly and exciting website for our land search company called "plotVista" This application will help individuals locate and or list lots for sale within the Caribbean. We will offer a small cash back incentive to buyers that purchase land from our site, and we will charge a 1%-2% success fee to our sellers once a successful transaction is made. We would like to become a match making site, matching buyers and sellers on our platform. We will also include a service directory and marketing advertisement spot for other service providers for a fee. We would like to see a webdesign incorporating Caribbean colors (blue, green and yellow) with very modern clean lines, very picturesque and easy to use.

Industry/Entity Type

Real Estate

Coding

Coded - Design and coding required

Number of Pages Required

5+ page

Font styles to use
Sans Serif

Colors
ffffff
85acd3
b768aa
dbdbdb

Requirements
Nice to have
• Scenic photos of the ocean and beautiful landscape

```html
<!DOCTYPE html>
<html lang="en">
<head>
<meta charset="utf-8">
<title>plotVista — Search Land Near By You</title>
<link href="https://fonts.googleapis.com/css2?family=Nunito+Sans:wght@400;600;700;800&family=Open+Sans:wght@400;600&display=swap" rel="stylesheet">
<style>
:root{
  --white:#ffffff;
  --sky:#85acd3;
  --orchid:#b768aa;
  --mist:#dbdbdb;
  --ink:#1d1d1d;
  --text:#6b6b6b;
  --footer:#111111;
  --sea-deep:#1f4f74;
  --sea:#2d6f93;
  --lagoon:#2f8a92;
  --lagoon-deep:#1d5f66;
  --photo-a:#5c93b5;
  --photo-b:#7fb0c9;
}
*{box-sizing:border-box;margin:0;padding:0}
html,body{width:1200px;height:3147px;overflow:hidden}
body{position:relative;font-family:"Open Sans",Arial,sans-serif;color:var(--text);background:var(--white)}
.head{font-family:"Nunito Sans",Arial,sans-serif}
section,header,footer{position:absolute;left:0;width:1200px}
.abs{position:absolute}

/* hero */
.hero{top:0;height:508px;background:linear-gradient(180deg,var(--sea) 0%,var(--sea-deep) 100%)}
.hero-photo{position:absolute;inset:0}
.brand{left:99px;top:30px;font-family:"Nunito Sans",sans-serif;font-weight:700;font-size:30px;color:var(--white)}
.top-phone{right:100px;top:12px;display:flex;align-items:center;gap:10px;color:var(--white);font-family:"Nunito Sans",sans-serif;font-weight:600;font-size:17px}
.nav{right:92px;top:56px;display:flex;gap:30px;font-family:"Nunito Sans",sans-serif;font-weight:700;font-size:16px;color:var(--white);align-items:center}
.nav .active{color:var(--orchid)}
.search{left:315px;top:168px;width:570px;height:193px;background:rgba(20,40,60,.72);padding:18px 22px}
.search h1{font-family:"Nunito Sans",sans-serif;font-weight:800;font-size:29px;color:var(--white);text-align:center;letter-spacing:.5px}
.field{background:var(--white);height:36px;border-radius:2px;font-size:12px;color:#888;padding:0 12px;display:flex;align-items:center;justify-content:space-between}
.field.full{margin-top:12px}
.row{display:flex;gap:10px;margin-top:10px}
.row .field{flex:1;height:32px}
.btn-search{margin-top:10px;height:38px;background:var(--orchid);color:var(--white);font-family:"Nunito Sans",sans-serif;font-weight:700;font-size:14px;display:flex;align-items:center;justify-content:center;gap:8px}
.dots{left:568px;top:444px;display:flex;gap:5px}
.dots span{width:13px;height:13px;border-radius:50%;border:2px solid var(--white)}
.dots span.on{background:var(--white)}

/* welcome */
.welcome{top:508px;height:415px}
.welcome h2{left:99px;top:50px;font-size:30px;font-weight:700;color:var(--ink)}
.welcome p{left:99px;width:490px;font-size:12.5px;line-height:24px}
.btn-ghost{border:2px solid var(--mist);border-radius:22px;color:var(--orchid);font-family:"Nunito Sans",sans-serif;font-weight:700;font-size:12px;display:flex;align-items:center;justify-content:center}
.map{left:646px;top:58px;width:453px;height:294px;border:5px solid #eee;background:#b3cdec}

/* banner */
.banner{top:923px;height:327px;background:linear-gradient(180deg,var(--lagoon) 0%,var(--lagoon-deep) 100%)}
.banner p{left:160px;width:880px;top:60px;text-align:center;color:var(--white);font-family:"Nunito Sans",sans-serif;font-weight:600;font-size:25px;line-height:41px}
.btn-post{left:501px;top:210px;width:198px;height:48px;border:2px solid var(--white);border-radius:26px;color:var(--white);font-family:"Nunito Sans",sans-serif;font-weight:700;font-size:15px;display:flex;align-items:center;justify-content:center;gap:8px}

/* services */
.services{top:1250px;height:480px}
.section-title{font-family:"Nunito Sans",sans-serif;font-weight:700;font-size:29px;color:var(--ink)}
.services .section-title{left:0;width:1200px;text-align:center;top:62px}
.service{width:260px;text-align:center}
.service svg{display:block;margin:0 auto}
.service h3{font-family:"Nunito Sans",sans-serif;font-weight:700;font-size:19px;color:var(--ink);margin-top:14px}
.service p{font-size:12.5px;line-height:22px;margin:6px auto 0;width:215px}
.divider{left:99px;top:478px;width:1000px;height:2px;background:var(--mist)}

/* properties */
.props{top:1730px;height:960px}
.props .section-title{left:99px;top:50px}
.prop{left:99px;width:1000px;height:214px}
.prop .photo{position:absolute;left:0;top:0;width:308px;height:214px;border:5px solid #eee;background:linear-gradient(180deg,var(--photo-b),var(--photo-a))}
.prop .info{position:absolute;left:354px;top:12px;width:640px}
.prop h3{font-family:"Nunito Sans",sans-serif;font-weight:800;font-size:19px;color:var(--ink);letter-spacing:.3px}
.prop .desc{font-size:13px;line-height:24px;margin-top:14px}
.prop .meta{font-family:"Nunito Sans",sans-serif;font-weight:600;font-size:16px;color:#444;margin-top:12px}
.prop .meta b{color:var(--orchid);font-weight:600}
.prop .meta i{font-style:normal;color:var(--orchid);margin:0 8px}
.prop .buy{display:flex;align-items:center;gap:32px;margin-top:10px}
.prop .price{font-family:"Nunito Sans",sans-serif;font-weight:800;font-size:19px;color:var(--ink)}
.prop .more{width:146px;height:40px;font-size:13px}
.pager{left:99px;top:895px;display:flex;gap:6px}
.pager span{width:20px;height:20px;font-size:11px;display:flex;align-items:center;justify-content:center;background:var(--mist);color:#444}
.pager .arrow{background:var(--sky);color:var(--white)}
.pager .cur{background:var(--orchid);color:var(--white)}

/* directory */
.directory{top:2709px;height:207px;background:var(--sky);color:var(--white)}
.dir-brand{left:99px;top:70px;display:flex;align-items:center;gap:14px;font-family:"Nunito Sans",sans-serif;font-weight:800;font-size:34px}
.dir-brand span.mark{width:34px;height:34px;border-radius:50%;border:3px solid var(--white)}
.directory h2{left:365px;top:38px;font-family:"Nunito Sans",sans-serif;font-weight:600;font-size:28px}
.directory p{left:365px;top:84px;width:740px;font-size:12.5px;line-height:22px}
.directory .more{left:365px;top:146px;font-family:"Nunito Sans",sans-serif;font-weight:700;font-size:13px}

/* footer */
.footer{top:2916px;height:231px;background:var(--footer);color:var(--white)}
.contacts{left:0;width:1200px;top:38px;display:flex;justify-content:center;gap:44px;font-size:13px}
.contact{display:flex;align-items:center;gap:14px;line-height:20px;color:var(--white)}
.contact span{color:var(--white)}
.ring{width:40px;height:40px;border-radius:50%;border:2px solid var(--white);display:flex;align-items:center;justify-content:center}
.foot-nav{left:0;width:1200px;top:110px;display:flex;justify-content:center;gap:18px;font-size:13.5px}
.foot-nav span{color:var(--white)}
.foot-nav i{font-style:normal;color:#888}
.foot-line{left:99px;top:162px;width:1000px;height:1px;background:#333}
.copy{left:99px;top:188px;font-size:12px;color:#ccc}
.social{right:112px;top:180px;display:flex;gap:10px}
.social span{width:34px;height:34px;border-radius:50%;border:1.5px solid var(--white)}
</style>
</head>
<body>

<header class="hero">
  <div class="hero-photo" role="img" aria-label="Scenic photograph of Caribbean islands and sea"></div>
  <div class="abs brand">plotVista</div>
  <div class="abs top-phone">
    <svg width="26" height="26" viewBox="0 0 26 26"><circle cx="13" cy="13" r="11.5" fill="none" stroke="#fff" stroke-width="1.6"/><path d="M9.5 8c1 0 1.6 2 1.6 2.5s-.9.8-.9 1.3c.4 1.4 1.6 2.6 3 3 .5 0 .8-.9 1.300-.9s2.5.6 2.5 1.6c0 1-1 1.8-2 1.8-3.6-.3-6.5-3.2-6.8-6.8 0-1 .8-2.5 1.300-2.5z" fill="#fff"/></svg>
    1 800 555 0142
  </div>
  <nav class="abs nav">
    <span class="active">Home</span><span>About</span><span>Buy</span><span>Sell</span><span>Landlords</span><span>Rent</span><span>Our services</span><span>Contact</span>
    <svg width="16" height="16" viewBox="0 0 16 16"><circle cx="6.5" cy="6.5" r="5" fill="none" stroke="#fff" stroke-width="2"/><path d="M10.3 10.3l4.5 4.5" stroke="#fff" stroke-width="2.4"/></svg>
  </nav>
  <form class="abs search">
    <h1>SEARCH LAND NEAR BY YOU</h1>
    <div class="field full">Search Location, Area Land...</div>
    <div class="row">
      <div class="field">Select Land Sqft <span>⌄</span></div>
      <div class="field">Max Price <span>⌄</span></div>
      <div class="field">Min Price <span>⌄</span></div>
    </div>
    <div class="btn-search">
      <svg width="13" height="13" viewBox="0 0 16 16"><circle cx="6.5" cy="6.5" r="5" fill="none" stroke="#fff" stroke-width="2.2"/><path d="M10.3 10.3l4.5 4.5" stroke="#fff" stroke-width="2.6"/></svg>
      SEARCH
    </div>
  </form>
  <div class="abs dots"><span class="on"></span><span></span><span></span><span></span></div>
</header>

<section class="welcome">
  <h2 class="abs head">Welcome to plotVista</h2>
  <p class="abs" style="top:108px">At vero eos et accusamus et iusto odio dignissimos ducimus qui blanditiis praesen iuvol up tatum deleniti atque corrupti quos dolores et quas.</p>
  <p class="abs" style="top:180px">Molestias excepturi sint occaecati cupiditate non provident, similique sunt in culp quise officia deserunt mollitia animi, id est laborum et dolorum fuga. Et harum quidem rerum facilis estet expedita distinctio. Nam libero tempore, cum soluta nobis est eligendi optio cumque nihil im pedit quo minus id quod maxime.</p>
  <div class="abs btn-ghost" style="left:99px;top:313px;width:128px;height:38px">READ MORE &gt;&gt;</div>
  <div class="abs map" role="img" aria-label="Map of the Caribbean with a location pin"></div>
</section>

<section class="banner" role="img" aria-label="Scenic photograph of a tropical lagoon">
  <p class="abs">We will offer a small cash back incentive to buyers that purchase land from our site, and we will charge a 1%-2% success fee to our sellers once a successful transaction is made.</p>
  <div class="abs btn-post">
    <svg width="14" height="14" viewBox="0 0 14 14"><path d="M7 1l4 4H8.5v4h-3V5H3z" fill="#fff"/><rect x="1" y="10.5" width="12" height="2.5" fill="#fff"/></svg>
    POST LAND
  </div>
</section>

<section class="services">
  <h2 class="abs section-title">Our Services</h2>

  <div class="abs service" style="left:65px;top:138px">
    <svg width="180" height="180" viewBox="0 0 180 180"><rect x="32" y="32" width="116" height="116" transform="rotate(45 90 90)" fill="#b768aa" stroke="#b768aa" stroke-width="4"/><rect x="40" y="40" width="100" height="100" transform="rotate(45 90 90)" fill="none" stroke="#fff" stroke-width="2"/><rect x="66" y="76" width="48" height="28" rx="2" fill="#fff"/><circle cx="90" cy="90" r="8" fill="#b768aa"/></svg>
    <h3>Buy Now</h3>
    <p>Neque porro quisquam est, qui do lorem ipsum quia dolor sit</p>
  </div>

  <div class="abs service" style="left:329px;top:138px">
    <svg width="180" height="180" viewBox="0 0 180 180"><rect x="32" y="32" width="116" height="116" transform="rotate(45 90 90)" fill="#fff" stroke="#b768aa" stroke-width="4"/><rect x="40" y="40" width="100" height="100" transform="rotate(45 90 90)" fill="none" stroke="#b768aa" stroke-width="1.5"/><path d="M68 76h8l6 20h22l5-14H80" fill="none" stroke="#85acd3" stroke-width="4"/><circle cx="85" cy="104" r="3.5" fill="#85acd3"/><circle cx="101" cy="104" r="3.5" fill="#85acd3"/></svg>
    <h3>Sell now</h3>
    <p>Neque porro quisquam est, qui do lorem ipsum quia dolor sit</p>
  </div>

  <div class="abs service" style="left:596px;top:138px">
    <svg width="180" height="180" viewBox="0 0 180 180"><rect x="32" y="32" width="116" height="116" transform="rotate(45 90 90)" fill="#fff" stroke="#b768aa" stroke-width="4"/><rect x="40" y="40" width="100" height="100" transform="rotate(45 90 90)" fill="none" stroke="#b768aa" stroke-width="1.5"/><rect x="66" y="76" width="48" height="28" rx="2" fill="#85acd3"/><circle cx="90" cy="90" r="8" fill="#fff"/></svg>
    <h3>Make Money</h3>
    <p>Neque porro quisquam est, qui do lorem ipsum quia dolor sit</p>
  </div>

  <div class="abs service" style="left:867px;top:138px">
    <svg width="180" height="180" viewBox="0 0 180 180"><rect x="32" y="32" width="116" height="116" transform="rotate(45 90 90)" fill="#fff" stroke="#b768aa" stroke-width="4"/><rect x="40" y="40" width="100" height="100" transform="rotate(45 90 90)" fill="none" stroke="#b768aa" stroke-width="1.5"/><circle cx="90" cy="90" r="18" fill="none" stroke="#85acd3" stroke-width="4"/></svg>
    <h3>Isleway Services</h3>
    <p>Neque porro quisquam est, qui do lorem ipsum quia dolor sit</p>
  </div>

  <div class="abs divider"></div>
</section>

<section class="props">
  <h2 class="abs section-title">Latest Property</h2>

  <article class="abs prop" style="top:131px">
    <div class="photo" role="img" aria-label="Property photograph of a coastal plot"></div>
    <div class="info">
      <h3>LOREM IPSUM DOLOR SIT UI BLANDITIIS PRAESENTIUM</h3>
      <p class="desc">At vero eos et accusamus et iusto odio dignissimos ducimus qui blanditiis praesentiumvol uptatum deleniti atque corrupti quos dolores et quas.</p>
      <div class="meta"><b>Location:</b> 27 Seabreeze Road <i>|</i><b>Area:</b> 2000Sft</div>
      <div class="buy"><span class="price">$210, 22, 000</span><span class="btn-ghost more">MORE DETAILS</span></div>
    </div>
  </article>

  <article class="abs prop" style="top:381px">
    <div class="photo" role="img" aria-label="Property photograph of a beachfront plot"></div>
    <div class="info">
      <h3>LOREM IPSUM DOLOR SIT UI BLANDITIIS PRAESENTIUM</h3>
      <p class="desc">At vero eos et accusamus et iusto odio dignissimos ducimus qui blanditiis praesentiumvol uptatum deleniti atque corrupti quos dolores et quas.</p>
      <div class="meta"><b>Location:</b> 27 Seabreeze Road <i>|</i><b>Area:</b> 2000Sft</div>
      <div class="buy"><span class="price">$210, 22, 000</span><span class="btn-ghost more">MORE DETAILS</span></div>
    </div>
  </article>

  <article class="abs prop" style="top:628px">
    <div class="photo" role="img" aria-label="Property photograph of a hillside villa by the sea"></div>
    <div class="info">
      <h3>LOREM IPSUM DOLOR SIT UI BLANDITIIS PRAESENTIUM</h3>
      <p class="desc">At vero eos et accusamus et iusto odio dignissimos ducimus qui blanditiis praesentiumvol uptatum deleniti atque corrupti quos dolores et quas.</p>
      <div class="meta"><b>Location:</b> 27 Seabreeze Road <i>|</i><b>Area:</b> 2000Sft</div>
      <div class="buy"><span class="price">$210, 22, 000</span><span class="btn-ghost more">MORE DETAILS</span></div>
    </div>
  </article>

  <div class="abs pager"><span class="arrow">«</span><span class="cur">1</span><span>2</span><span>3</span><span>4</span><span class="arrow">»</span></div>
</section>

<section class="directory">
  <div class="abs dir-brand"><span class="mark"></span>ISLEWAY</div>
  <h2 class="abs">Isleway Service Directory</h2>
  <p class="abs">Nam libero tempore, cum soluta nobis est eligendi optio cumque nihil impedit quo minus id quod maxime placeat facere possimus, omnis voluptas assumenda est, omnis dolor repellendus igen.</p>
  <div class="abs more">READ MORE &gt;&gt;</div>
</section>

<footer class="footer">
  <div class="abs contacts">
    <div class="contact"><span class="ring"><svg width="14" height="18" viewBox="0 0 14 18"><path d="M7 1a6 6 0 0 1 6 6c0 4.5-6 10-6 10S1 11.5 1 7a6 6 0 0 1 6-6z" fill="#fff"/><circle cx="7" cy="7" r="2.2" fill="#111"/></svg></span><span>412 Harbour View Lane<br>Port Coral, PC 20418</span></div>
    <div class="contact"><span class="ring"><svg width="16" height="16" viewBox="0 0 16 16"><path d="M3 1c1.3 0 2.3 3 2.3 3.6S4 5.8 4 6.5c.6 2 2.3 3.7 4.3 4.3.7 0 1.2-1.3 1.9-1.3S15 10.4 15 11.7c0 1.4-1.4 2.6-2.7 2.6C7 14 2 9 1.7 3.7 1.7 2.4 2.3 1 3 1z" fill="#fff"/></svg></span><span>1 800 555 0142</span></div>
    <div class="contact"><span class="ring"><svg width="18" height="14" viewBox="0 0 18 14"><rect x="1" y="1" width="16" height="12" rx="1.5" fill="#fff"/><path d="M1.5 2l7.5 6 7.5-6" fill="none" stroke="#111" stroke-width="1.6"/></svg></span><span>info@plotvista.com</span></div>
  </div>
  <nav class="abs foot-nav">
    <span>Home</span><i>|</i><span>About</span><i>|</i><span>Buy</span><i>|</i><span>Sell</span><i>|</i><span>Landlords</span><i>|</i><span>Rent</span><i>|</i><span>Our services</span><i>|</i><span>Contact</span>
  </nav>
  <div class="abs foot-line"></div>
  <div class="abs copy">Copyrights © 2017, plotVista . All rights reserved.</div>
  <div class="abs social" aria-label="Social links"><span></span><span></span><span></span><span></span></div>
</footer>

</body>
</html>
```